Header Card Design for Marine Tool Product

We package up our small tools in bags. A nice header card would finish the look.
* Bag is 4" wide. Header Card should be 4x4, folded to 4x2
* Back of card should have 2.25x1.25 area for our part number sticker.
* Design to reinforce the brand and add (perception of) quality to the product.

Brand Website: harbolvex.com

Target Market(s)

Boat Mechanics/Boat owners

Industry/Entity Type

```html
<!DOCTYPE html>
<html lang="en">
<head>
<meta charset="UTF-8">
<title>Harbolvex Header Card</title>
<link href="https://fonts.googleapis.com/css2?family=Montserrat:ital,wght@0,400;0,800;1,800&display=swap" rel="stylesheet">
<style>
  :root {
    --navy: #13204a;
    --teal-ink: #0f4d5c;
    --cyan: #4fc6d6;
    --rule: #9a9a9a;
    --ink: #2a2a2a;
    --paper: #ffffff;
  }
  * { box-sizing: border-box; margin: 0; padding: 0; }
  html, body { width: 1200px; height: 840px; overflow: hidden; background: var(--paper); }
  body { position: relative; font-family: "Montserrat", Arial, sans-serif; }

  .header-card {
    position: absolute; left: 320px; top: 140px;
    width: 560px; height: 560px;
    border: 1px solid var(--rule);
    background: var(--paper);
  }
  .panel { position: absolute; left: 0; width: 100%; height: 280px; }
  .panel--back { top: 0; border-bottom: 1.5px solid var(--rule); }
  .panel--front { top: 280px; }

  .hang-hole { position: absolute; left: 212px; width: 136px; height: 54px; }
  .panel--back .hang-hole { top: 210px; }
  .panel--front .hang-hole { top: 16px; }

  .sticker-area {
    position: absolute; left: 227px; top: 17px;
    width: 314px; height: 175px;
    border: 2px solid #111; border-radius: 10px;
  }
  .upside-down { transform: rotate(180deg); }

  .company-address {
    position: absolute; left: 20px; top: 44px; width: 180px;
    font-size: 13px; line-height: 17.8px; color: var(--ink);
    text-align: left; white-space: nowrap;
  }
  .back-brand {
    position: absolute; left: 88px; top: 172px; width: 112px;
    display: flex; align-items: center; justify-content: center; gap: 5px;
    font-weight: 800; font-size: 14px; color: var(--navy); letter-spacing: 0.5px;
  }
  .brand-dot { width: 9px; height: 9px; border-radius: 50%; background: var(--cyan); flex: none; }

  .brand-name {
    position: absolute; left: 150px; top: 128px; width: 260px;
    display: flex; align-items: center; justify-content: center; gap: 10px;
    font-weight: 800; font-size: 36px; color: var(--navy); letter-spacing: 1px;
  }
  .brand-name .brand-dot { width: 18px; height: 18px; }

  .feature-list { position: absolute; top: 100px; display: flex; flex-direction: column; gap: 9px; }
  .feature-list--left { left: 18px; }
  .feature-list--right { left: 430px; }
  .feature { display: flex; align-items: center; gap: 4px; }
  .feature svg { width: 24px; height: 24px; flex: none; }
  .feature-label {
    font-weight: 800; font-style: italic; font-size: 15px; line-height: 15px;
    color: var(--teal-ink);
  }

  .tagline-band {
    position: absolute; left: -1px; right: -1px; bottom: 0; height: 42px;
    background: var(--cyan);
    display: flex; align-items: center; justify-content: center;
    font-weight: 800; font-style: italic; font-size: 17.5px; color: var(--navy);
    letter-spacing: 0.2px;
  }
</style>
</head>
<body>
  <div class="header-card">

    <section class="panel panel--back">
      <div class="sticker-area" aria-label="Part number sticker area"></div>
      <div class="company-address upside-down">
        <p>Company Address</p>
        <p>Here xxxxxxxxxxxxxx</p>
        <p>xxxxxxxxxxxxxxxxxxx</p>
        <p>harbolvex.com</p>
        <p>info@harbolvex.com</p>
        <p>Tel: 01 0000 0000</p>
      </div>
      <div class="back-brand upside-down"><span class="brand-dot"></span>HARBOLVEX</div>
      <svg class="hang-hole" viewBox="0 0 136 54" aria-hidden="true">
        <path d="M16 1 H120 A15 15 0 0 1 120 31 H88 A20 20 0 0 1 48 31 H16 A15 15 0 0 1 16 1 Z"
              fill="none" stroke="#111" stroke-width="1.2"/>
      </svg>
    </section>

    <section class="panel panel--front">
      <svg class="hang-hole" viewBox="0 0 136 54" aria-hidden="true">
        <path d="M16 53 H120 A15 15 0 0 0 120 23 H88 A20 20 0 0 0 48 23 H16 A15 15 0 0 0 16 53 Z"
              fill="none" stroke="#111" stroke-width="1.2"/>
      </svg>

      <ul class="feature-list feature-list--left">
        <li class="feature">
          <svg viewBox="0 0 24 24" fill="none" stroke="var(--cyan)" stroke-width="1.4" stroke-linecap="round">
            <path d="M9 17h6M10 20h4M12 6a5 5 0 0 0-3 9v2h6v-2a5 5 0 0 0-3-9z"/>
            <path d="M12 1v2M4 4l1.5 1.5M20 4l-1.5 1.5M1 11h2M21 11h2"/>
          </svg>
          <span class="feature-label">Innovative<br>Design</span>
        </li>
        <li class="feature">
          <svg viewBox="0 0 24 24" fill="none" stroke="var(--cyan)" stroke-width="1.4" stroke-linecap="round">
            <circle cx="12" cy="9" r="7"/><circle cx="12" cy="9" r="3.5"/>
            <path d="M8 15l-2 7 3-2 2 3M16 15l2 7-3-2-2 3"/>
          </svg>
          <span class="feature-label">Lifetime<br>Warranty</span>
        </li>
      </ul>

      <div class="brand-name"><span class="brand-dot"></span>HARBOLVEX</div>

      <ul class="feature-list feature-list--right">
        <li class="feature">
          <svg viewBox="0 0 24 24" fill="none" stroke="var(--cyan)" stroke-width="1.4" stroke-linecap="round">
            <path d="M10 8l3-3a3.5 3.5 0 0 1 5 5l-3 3M14 16l-3 3a3.5 3.5 0 0 1-5-5l3-3"/>
            <path d="M3 8h3M8 3v3M21 16h-3M16 21v-3"/>
          </svg>
          <span class="feature-label">Super<br>Tough</span>
        </li>
        <li class="feature">
          <svg viewBox="0 0 24 24" fill="none" stroke="var(--cyan)" stroke-width="1.4" stroke-linecap="round">
            <circle cx="12" cy="13" r="8"/><path d="M12 8v5l3 2M20 4l2 2M10 3h4"/>
          </svg>
          <span class="feature-label">Time<br>Saving</span>
        </li>
      </ul>

      <div class="tagline-band">SPECIALTY TOOLS FOR MARINE MECHANICS</div>
    </section>

  </div>
</body>
</html>
```